Copperleaf Roofing Business Card

This is my current business card. But I’d like to make some changes. Somewhere on the card I’d like to list some of the services we offer. Maybe on the back? But I’d still like to keep the red. White and black modern look.

-residential & commercial roofing
-Roof Repairs & Maintenance
-Storm Damage & Insurance Claims specialist
-Christmas Lights and permanent Christmas lights
Fencing. Windows. Gutters. Siding. Sheetrock, painting.

```html
<!DOCTYPE html>
<html lang="en">
<head>
<meta charset="utf-8">
<title>Copperleaf Roofing Co. — Business Card</title>
<link href="https://fonts.googleapis.com/css2?family=Michroma&family=Open+Sans:wght@400;700&family=Oswald:wght@400;500&display=swap" rel="stylesheet">
<style>
  :root {
    --stage: #3a3a3a;
    --card-black: #050505;
    --brand-red: #e3232a;
    --deep-red: #7a0d10;
    --mid-red: #b8161b;
    --white: #ffffff;
    --soft-white: #f1f1f1;
  }
  * { box-sizing: border-box; margin: 0; padding: 0; }
  html, body { width: 1200px; height: 1200px; overflow: hidden; }
  body {
    background: var(--stage);
    display: flex;
    flex-direction: column;
    align-items: center;
    justify-content: center;
    gap: 60px;
    font-family: "Open Sans", sans-serif;
  }
  .card {
    position: relative;
    width: 900px;
    height: 514px;
    border-radius: 34px;
    overflow: hidden;
  }

  /* Front */
  .card-front { background: var(--card-black); }
  .front-band {
    position: absolute;
    left: 0; right: 0; bottom: 0;
    height: 70px;
    background: linear-gradient(90deg, var(--deep-red), var(--brand-red) 35%, var(--mid-red) 65%, var(--deep-red));
  }
  .contact-block {
    position: absolute;
    left: 60px;
    top: 175px;
    width: 420px;
    color: var(--white);
  }
  .person-name {
    font-family: "Michroma", sans-serif;
    font-weight: 400;
    font-size: 28px;
    letter-spacing: 0.5px;
    line-height: 1;
    white-space: nowrap;
  }
  .person-name .first { color: var(--brand-red); }
  .person-name .last { color: var(--white); }
  .person-role {
    margin-top: 14px;
    font-size: 20px;
  }
  .person-role .region { color: var(--brand-red); }
  .contact-list {
    list-style: none;
    margin-top: 22px;
    font-size: 20px;
    letter-spacing: 0.5px;
  }
  .contact-list li {
    display: flex;
    align-items: center;
    gap: 12px;
    margin-bottom: 10px;
  }
  .contact-list svg { width: 22px; height: 22px; flex: none; }

  .brand-block {
    position: absolute;
    left: 515px;
    top: 60px;
    width: 360px;
  }
  .brand-lockup {
    display: flex;
    align-items: center;
    gap: 12px;
  }
  .brand-dot {
    width: 44px; height: 44px;
    border-radius: 50%;
    background: var(--brand-red);
    flex: none;
  }
  .brand-name {
    font-family: "Open Sans", sans-serif;
    font-weight: 700;
    font-size: 24px;
    line-height: 1.1;
    color: var(--white);
    letter-spacing: 1px;
    text-transform: uppercase;
  }
  .service-list {
    list-style: none;
    margin-top: 28px;
    font-family: "Oswald", sans-serif;
    font-size: 15.5px;
    color: var(--soft-white);
    text-transform: uppercase;
    line-height: 1.5;
    white-space: nowrap;
  }
  .service-item::before,
  .service-chip::before {
    content: "";
    display: inline-block;
    width: 6px; height: 6px;
    border-radius: 50%;
    background: var(--brand-red);
    margin-right: 8px;
    vertical-align: middle;
  }
  .service-chip { margin-right: 12px; }

  /* Back */
  .card-back { background: var(--mid-red); }
  .back-pattern {
    position: absolute;
    inset: 0;
    background: linear-gradient(135deg, var(--deep-red) 0%, var(--brand-red) 35%, var(--mid-red) 60%, var(--deep-red) 100%);
  }
  .back-lockup {
    position: absolute;
    inset: 0;
    display: flex;
    flex-direction: column;
    align-items: center;
    justify-content: center;
    gap: 26px;
  }
  .back-mark {
    width: 190px; height: 190px;
    border-radius: 50%;
    background: var(--card-black);
  }
  .back-name {
    font-family: "Open Sans", sans-serif;
    font-weight: 700;
    font-size: 46px;
    line-height: 1.1;
    color: var(--white);
    letter-spacing: 2px;
    text-transform: uppercase;
    text-align: center;
  }
</style>
</head>
<body>

  <section class="card card-front">
    <div class="contact-block">
      <h1 class="person-name"><span class="first">DANA</span> <span class="last">WHITFIELD</span></h1>
      <p class="person-role">Roofing contractor in <span class="region">Texas</span></p>
      <ul class="contact-list">
        <li>
          <svg viewBox="0 0 24 24" aria-hidden="true"><path fill="#e3232a" d="M6.6 10.8a15 15 0 0 0 6.6 6.6l2.2-2.2c.3-.3.7-.4 1-.2 1.1.4 2.3.6 3.6.6.6 0 1 .4 1 1V20c0 .6-.4 1-1 1A17 17 0 0 1 3 4c0-.6.4-1 1-1h3.5c.6 0 1 .4 1 1 0 1.3.2 2.5.6 3.6.1.3 0 .7-.2 1z"/></svg>
          682-555-0148
        </li>
        <li>
          <svg viewBox="0 0 24 24" aria-hidden="true"><rect x="2" y="5" width="20" height="14" fill="#e3232a"/><path d="M2 5l10 8 10-8" fill="none" stroke="#050505" stroke-width="2"/></svg>
          dana@copperleafroofing.co
        </li>
        <li>
          <svg viewBox="0 0 24 24" aria-hidden="true"><circle cx="12" cy="12" r="9" fill="none" stroke="#e3232a" stroke-width="2"/><path d="M3 12h18M12 3c3 3 3 15 0 18M12 3c-3 3-3 15 0 18" fill="none" stroke="#e3232a" stroke-width="1.6"/></svg>
          www.copperleafroofing.co
        </li>
      </ul>
    </div>

    <div class="brand-block">
      <div class="brand-lockup">
        <span class="brand-dot" aria-hidden="true"></span>
        <span class="brand-name">Copperleaf<br>Roofing Co.</span>
      </div>
      <ul class="service-list">
        <li class="service-item">Residential &amp; Commercial Roofing</li>
        <li class="service-item">Roof Repairs &amp; Maintenance</li>
        <li class="service-item">Storm Damage &amp; Insurance Claims Specialist</li>
        <li class="service-item">Christmas Lights and Permanent Christmas Lights</li>
        <li><span class="service-chip">Fencing</span><span class="service-chip">Windows</span><span class="service-chip">Gutters</span></li>
        <li><span class="service-chip">Siding</span><span class="service-chip">Sheetrock</span><span class="service-chip">Painting.</span></li>
      </ul>
    </div>

    <div class="front-band" role="img" aria-label="Red, black and white tartan plaid band"></div>
  </section>

  <section class="card card-back">
    <div class="back-pattern" role="img" aria-label="Red, black and white tartan plaid background"></div>
    <div class="back-lockup">
      <span class="back-mark" aria-hidden="true"></span>
      <p class="back-name">Copperleaf<br>Roofing Co.</p>
    </div>
  </section>

</body>
</html>
```